Veldmark Supplies Business Card

Professional business card that stand out to our potential customers. Front and back with clean modern design

Industry/Entity Type

Oil and gas

Contact Information for Business Card

Name, address, website , office phone and cell number

Requirements
Must have
• Editable files for each employee

```html
<!DOCTYPE html>
<html lang="en">
<head>
<meta charset="utf-8">
<title>Veldmark Supplies Business Card</title>
<link rel="stylesheet" href="https://fonts.googleapis.com/css2?family=Roboto:wght@400;500;700&display=swap">
<style>
  :root {
    --stage: #d9d9db;
    --card-black: #1c1d1f;
    --card-ink: #232427;
    --brand-red: #e41e26;
    --brand-blue: #27a9d6;
    --text-light: #e9e9ea;
    --text-muted: #b9babd;
    --gloss: #3a3b3e;
  }
  * { box-sizing: border-box; margin: 0; padding: 0; }
  html, body { width: 1200px; height: 852px; overflow: hidden; }
  body {
    background: var(--stage);
    font-family: "Roboto", Arial, sans-serif;
    position: relative;
  }
  .card {
    position: absolute;
    top: 271px;
    width: 540px;
    height: 310px;
    border-radius: 26px;
    overflow: hidden;
    background: var(--card-black);
  }
  .card--front { left: 40px; }
  .card--back { left: 620px; background: var(--card-ink); }

  /* Front */
  .front-brand {
    position: absolute;
    inset: 0;
    display: flex;
    align-items: center;
    justify-content: center;
    gap: 14px;
  }
  .front-brand__mark {
    width: 26px; height: 26px;
    background: var(--gloss);
  }
  .front-brand__name {
    font-weight: 700;
    font-size: 30px;
    letter-spacing: 2px;
    text-transform: uppercase;
    color: var(--gloss);
  }

  /* Back */
  .back-art { position: absolute; inset: 0; width: 540px; height: 310px; }
  .holder {
    position: absolute;
    right: 30px;
    top: 22px;
    text-align: right;
    color: #fff;
  }
  .holder__name { font-weight: 700; font-size: 21px; line-height: 1.1; }
  .holder__title { font-size: 12px; margin-top: 3px; }

  .contact {
    position: absolute;
    right: 26px;
    top: 150px;
    list-style: none;
    color: var(--text-light);
    font-size: 12.5px;
    line-height: 1.35;
    text-align: right;
  }
  .contact__item {
    display: flex;
    justify-content: flex-end;
    align-items: center;
    gap: 8px;
    margin-bottom: 6px;
  }
  .contact__item--address { margin-bottom: 16px; }
  .contact__icon { width: 13px; height: 13px; flex: none; }

  .back-brand {
    position: absolute;
    left: 28px;
    bottom: 30px;
    display: flex;
    align-items: center;
    gap: 10px;
  }
  .back-brand__mark {
    width: 22px; height: 22px;
    background: var(--brand-red);
  }
  .back-brand__name {
    font-weight: 700;
    font-size: 22px;
    letter-spacing: 1.5px;
    text-transform: uppercase;
    color: #fff;
  }
</style>
</head>
<body>

<section class="card card--front" aria-label="Card front">
  <div class="front-brand">
    <span class="front-brand__mark"></span>
    <span class="front-brand__name">Veldmark Supplies</span>
  </div>
</section>

<section class="card card--back" aria-label="Card back">
  <svg class="back-art" viewBox="0 0 540 310" aria-hidden="true">
    <path fill="var(--brand-red)" d="M0,0 H540 V42 C430,70 300,88 190,130 C110,160 50,195 0,225 Z"/>
    <path fill="var(--brand-blue)" d="M0,250 C70,205 150,168 250,140 C350,112 450,98 540,66 V80 C440,112 350,128 258,152 C160,180 80,220 0,266 Z"/>
  </svg>

  <div class="holder">
    <p class="holder__name">Marten Hale</p>
    <p class="holder__title">Managing Director</p>
  </div>

  <ul class="contact">
    <li class="contact__item contact__item--address">
      <span>412 Ridgeline Ave Suite 5<br>Midland, Tx 79701</span>
      <svg class="contact__icon" viewBox="0 0 14 14"><path fill="var(--brand-red)" d="M7 0a5 5 0 0 0-5 5c0 3.5 5 9 5 9s5-5.5 5-9a5 5 0 0 0-5-5zm0 7a2 2 0 1 1 0-4 2 2 0 0 1 0 4z"/></svg>
    </li>
    <li class="contact__item">
      <span>(555)310-0418</span>
      <svg class="contact__icon" viewBox="0 0 14 14"><path fill="var(--brand-red)" d="M3 1l2.2 2.6-1.3 1.6c.8 1.8 2.1 3.1 3.9 3.9l1.6-1.3L12 10l-1.2 2.4C6 12.4 1.6 8 1.6 3.2z"/></svg>
    </li>
    <li class="contact__item">
      <span>sales@veldmarksupplies.com</span>
      <svg class="contact__icon" viewBox="0 0 14 14"><rect x="1" y="3" width="12" height="8" fill="var(--brand-red)"/><path d="M1 3l6 5 6-5" stroke="var(--card-ink)" stroke-width="1.2" fill="none"/></svg>
    </li>
    <li class="contact__item">
      <span>www.veldmarksupplies.com</span>
      <svg class="contact__icon" viewBox="0 0 14 14"><circle cx="7" cy="7" r="6" fill="var(--brand-red)"/><path d="M1 7h12M7 1c-2.5 3-2.5 9 0 12M7 1c2.5 3 2.5 9 0 12" stroke="var(--card-ink)" stroke-width="1" fill="none"/></svg>
    </li>
  </ul>

  <div class="back-brand">
    <span class="back-brand__mark"></span>
    <span class="back-brand__name">Veldmark Supplies</span>
  </div>
</section>

</body>
</html>
```